Reach Crafters Unique Marketing Website Design

I am starting a new company that is a thought leader in the marketing consulting space. The company is called Reach Crafters. We intend to build a Wordpress site on the Astra Theme with the Spectra builder. Our goal is to become the leading voice that empowers high-ticket service business leaders to become Reach Crafters by equipping them with the cutting-edge frameworks and decision grade intelligence taught in leading business schools. What we are looking for is a website design that is clean and professional, making some use of white space well also being eye catching and distinctive in the consulting space. We will probably want to have a video on the homepage not in the hero section, but just below to explain the company and what we do. Our tagline is "Be found. Be chosen." I have attached a brand guide with some messaging, our typography choices, and our color system. The full site will have a primary nav that is four pages - About us, Services, Insights (essentially a blog), and Contact Us. The goal of this project is to develop an art direction that I can give to a designer to build loads of new pages.

Target Market(s)

Business owners (mostly male) from 30-60 years old, looking to fix their sales and marketing funnel.

Industry/Entity Type

Marketing consulting

Font styles to use
Sans Serif

Requirements
Must have
• A clean, professional design that builds trust with owners of high-ticket service businesses. We need a space for explainer video, and sections that tell prospects what we do. Would also like to have a blog carousel.
Nice to have
• Social feeds, if possible. See attached documents for colors and fonts.
Should not have
• Our feel is professional enough to be trustworthy, but unique enough to be memorable. Cartoon ideas do not meet the professional test, and we do not want the website to appear feminine.

```html
<!DOCTYPE html>
<html lang="en">
<head>
<meta charset="UTF-8">
<title>Reach Crafters — Be Found. Be Chosen.</title>
<link rel="stylesheet" href="https://fonts.googleapis.com/css2?family=Oswald:wght@500;600;700&family=Inter:wght@400;500;600&display=swap">
<style>
:root{
  --navy:#07142e;
  --navy-2:#0d2350;
  --red:#ef4a4c;
  --red-soft:#e9474f;
  --purple:#8b5cf6;
  --purple-deep:#7c3aed;
  --ink:#141414;
  --grey:#5b5b5b;
  --white:#ffffff;
  --card-top:#9a4fd8;
  --card-bottom:#e1465a;
}
*{box-sizing:border-box;margin:0;padding:0}
html,body{width:1200px;height:5222px;overflow:hidden}
body{position:relative;background:var(--white);font-family:"Inter",Arial,sans-serif;color:var(--ink)}
.abs{position:absolute}
.heading{font-family:"Oswald","Arial Narrow",sans-serif;font-weight:600;text-transform:uppercase;letter-spacing:.5px;color:var(--ink)}
.center{left:0;width:1200px;text-align:center}
.btn{position:absolute;display:flex;align-items:center;justify-content:center;border-radius:30px;color:var(--white);font-size:15px;font-weight:500}
.btn-red{background:var(--red)}
.btn-purple{background:var(--purple)}
.photo{position:absolute;overflow:hidden}

/* hero */
.hero-bg{position:absolute;left:0;top:0;width:1200px;height:900px}
.logo{position:absolute;left:111px;top:32px;color:var(--white);font-size:33px;font-weight:600;letter-spacing:1px}
.nav{position:absolute;top:42px;left:522px;display:flex;gap:0}
.nav a{color:var(--white);font-size:15.5px;text-decoration:none;position:absolute;white-space:nowrap}
.nav a.active{color:var(--red)}
.nav-rule{position:absolute;left:522px;top:95px;width:567px;height:1px;background:rgba(255,255,255,.25)}
.hero-be{position:absolute;left:108px;top:186px;font-family:"Oswald",sans-serif;font-weight:700;font-size:128px;line-height:1;color:var(--white)}
.hero-words{position:absolute;left:253px;top:192px;font-family:"Oswald",sans-serif;font-weight:600;font-size:54px;line-height:58px;color:var(--white)}
.hero-lead{position:absolute;left:111px;top:324px;width:430px;color:var(--white);font-size:15px;line-height:28px}
.hero-note{position:absolute;left:111px;top:430px;width:396px;height:84px;border-radius:12px;background:rgba(255,255,255,.08);border-left:4px solid var(--red);padding:16px 24px;color:var(--white);font-size:15px;line-height:27px}

/* intro */
.intro-text{top:928px;left:262px;width:676px;text-align:center;color:var(--grey);font-size:15.5px;line-height:29px}
.feature{position:absolute;display:flex;align-items:flex-start;gap:30px}
.feature .dot{width:66px;height:66px;border-radius:50%;background:var(--red);display:flex;align-items:center;justify-content:center;box-shadow:0 6px 14px rgba(239,74,76,.3)}
.feature h4{font-size:16px;font-weight:600;letter-spacing:.5px;color:#333;margin-top:4px}
.feature p{font-size:14.5px;color:var(--grey);margin-top:10px}

/* video */
.video{left:111px;top:1178px;width:978px;height:540px;border-radius:40px;background:linear-gradient(160deg,#3a2d22 0%,#6b5238 40%,#2b2420 100%);box-shadow:0 8px 24px rgba(0,0,0,.15)}
.video .screen{position:absolute;left:185px;top:95px;width:610px;height:250px;border-radius:6px;background:linear-gradient(135deg,#1f3a6b,#3e4f8c 55%,#c0603a)}
.play{position:absolute;left:456px;top:238px;width:66px;height:66px;border-radius:50%;background:var(--purple);display:flex;align-items:center;justify-content:center}

/* services cards */
.card{position:absolute;top:1895px;width:313px;height:372px;border-radius:26px;background:linear-gradient(170deg,var(--card-top) 0%,#c04c9a 55%,var(--card-bottom) 100%);box-shadow:0 8px 20px rgba(0,0,0,.15);padding:0 38px;color:var(--white)}
.card .icon{position:absolute;left:38px;top:50px;width:74px;height:74px;border-radius:50%;background:var(--white);display:flex;align-items:center;justify-content:center}
.card h3{position:absolute;left:38px;top:150px;font-family:"Oswald",sans-serif;font-weight:600;font-size:24px}
.card p{position:absolute;left:38px;top:194px;width:240px;font-size:13.5px;line-height:27px}

/* testimonial */
.testi-bg{position:absolute;left:0;top:2360px;width:1200px;height:800px}
.quote-rule{position:absolute;left:400px;top:2558px;width:3px;height:300px;background:var(--white)}
.testi-text{position:absolute;left:466px;top:2580px;width:572px;color:var(--white);font-size:15px;line-height:27px;text-align:justify}
.testi-name{position:absolute;left:466px;top:2780px;color:var(--white);font-family:"Oswald",sans-serif;font-weight:500;font-size:19px}
.stars{position:absolute;left:466px;top:2812px;color:#f5a623;font-size:14px;letter-spacing:1px}

.banner{position:absolute;left:111px;top:2943px;width:978px;height:408px;border-radius:34px;background:linear-gradient(180deg,#e9474d,#e84a52);border:2px solid rgba(255,255,255,.7);box-shadow:0 10px 24px rgba(0,0,0,.15);color:var(--white);text-align:center}
.banner h2{position:absolute;left:0;width:100%;top:58px;font-family:"Oswald",sans-serif;font-weight:600;font-size:46px}
.banner p{position:absolute;left:130px;width:718px;top:126px;font-size:15.5px;line-height:29px}
.banner .checks{position:absolute;left:0;width:100%;top:226px;display:flex;justify-content:center;gap:60px;font-size:16px;font-weight:500;letter-spacing:.5px}
.banner .checks span{display:flex;align-items:center;gap:16px}

/* how we work */
.work-text{position:absolute;left:111px;top:3620px;width:390px;color:var(--grey);font-size:15.5px;line-height:30px;text-align:justify}
.work-list{position:absolute;left:150px;top:3756px;list-style:none}
.work-list li{display:flex;align-items:center;gap:18px;font-size:15.5px;height:36px}

/* insights */
.post{position:absolute;top:4186px;width:313px}
.post .thumb{width:313px;height:341px;border-radius:26px}
.post p{margin-top:28px;text-align:center;font-size:15.5px;line-height:27px;color:var(--ink)}

/* footer */
.foot-bg{position:absolute;left:0;top:4790px;width:1200px;height:432px}
.foot-logo{top:4942px;color:var(--white);font-size:42px;font-weight:600;letter-spacing:1px}
.foot-nav{position:absolute;top:5024px;left:0;width:1200px;display:flex;justify-content:center;align-items:center;color:var(--white);font-size:15.5px}
.foot-nav .sep{margin:0 48px;opacity:.9}
.socials{position:absolute;top:5083px;left:540px;display:flex;gap:12px}
.socials span{width:32px;height:32px;border-radius:50%;background:var(--red)}
.copy{top:5168px;color:var(--white);font-size:11px}
</style>
</head>
<body>

<!-- HERO -->
<svg class="hero-bg" viewBox="0 0 1200 900" aria-hidden="true">
  <defs>
    <linearGradient id="heroGrad" x1="0" y1="0" x2="1" y2="1">
      <stop offset="0" stop-color="#0a1a3c"/>
      <stop offset=".6" stop-color="#06122b"/>
      <stop offset="1" stop-color="#0b2a5c"/>
    </linearGradient>
  </defs>
  <path d="M0 0H1200V640Q640 830 0 585Z" fill="url(#heroGrad)"/>
  <path d="M60 612Q600 880 1200 650V632Q630 820 0 585Z" fill="var(--red)"/>
</svg>
<div class="photo" role="img" aria-label="Glowing digital rocket launching from a cloud of data particles" style="left:640px;top:30px;width:560px;height:650px;border-radius:0;background:radial-gradient(ellipse at 60% 55%,rgba(64,170,255,.55) 0%,rgba(30,100,200,.25) 35%,rgba(10,30,70,0) 70%)"></div>

<div class="logo">REACH CRAFTERS</div>
<nav class="nav">
  <a class="active" style="left:0">HOME</a>
  <a style="left:94px">ABOUT US</a>
  <a style="left:222px">SERVICES</a>
  <a style="left:342px">INSIGHTS</a>
  <a style="left:463px">CONTACT US</a>
</nav>
<div class="nav-rule"></div>

<div class="hero-be">BE</div>
<div class="hero-words">FOUND<br>CHOSEN</div>
<p class="hero-lead">Reach Crafters equips leaders with the frameworks, insight, and strategic clarity taught in the world's leading business schools</p>
<div class="hero-note">Decision-grade marketing intelligence for high-ticket service businesses.</div>
<a class="btn btn-red" style="left:111px;top:547px;width:230px;height:49px">Explore Our Approach</a>

<!-- INTRO -->
<h2 class="abs heading center" style="top:862px;font-size:44px">What is Reach Crafters?</h2>
<p class="abs intro-text">We help high-ticket service businesses build demand with precision—using rigorous frameworks, market insight, and strategic thinking typically reserved for elite business schools.</p>

<div class="feature" style="left:194px;top:1053px">
  <div class="dot"><svg width="28" height="28" viewBox="0 0 24 24"><circle cx="12" cy="12" r="10" fill="#fff"/><path d="M7 12.5l3.2 3L17 9" stroke="var(--red)" stroke-width="2.4" fill="none" stroke-linecap="round"/></svg></div>
  <div><h4>DECISION-GRADE INTELLIGENCE™</h4><p>Frameworks inspired by leading schools</p></div>
</div>
<div class="feature" style="left:641px;top:1043px">
  <div class="dot" style="margin-top:10px"><svg width="28" height="28" viewBox="0 0 24 24"><circle cx="12" cy="12" r="10" fill="#fff"/><path d="M7 12.5l3.2 3L17 9" stroke="var(--red)" stroke-width="2.4" fill="none" stroke-linecap="round"/></svg></div>
  <div><h4>HIGH-TICKET SERVICE LEADERS</h4><p>Strategy before tactics</p></div>
</div>

<!-- VIDEO -->
<div class="photo video" role="img" aria-label="Explainer video: team meeting in a boardroom reviewing marketing dashboards">
  <div class="screen"></div>
  <div class="play"><svg width="22" height="22" viewBox="0 0 24 24"><path d="M7 4l13 8-13 8z" fill="#fff"/></svg></div>
</div>

<!-- WHAT WE HELP YOU DO -->
<h2 class="abs heading center" style="top:1800px;font-size:44px">What we help you do</h2>

<div class="card" style="left:111px">
  <div class="icon"><svg width="38" height="38" viewBox="0 0 24 24"><circle cx="13" cy="10" r="6" fill="none" stroke="var(--red)" stroke-width="2"/><circle cx="13" cy="10" r="2.4" fill="var(--red)"/><path d="M8.5 14.5L3 20" stroke="var(--purple)" stroke-width="2.4" stroke-linecap="round"/></svg></div>
  <h3>BE FOUND</h3>
  <p>Sed ut perspiciatis unde omnis iste natus error sit voluptatem accusa nt ium doloremque laudant ium, totam rem aperiam, eaque ipsa quae ab illo inventore</p>
</div>
<div class="card" style="left:444px">
  <div class="icon"><svg width="38" height="38" viewBox="0 0 24 24"><rect x="5" y="3" width="14" height="18" rx="4" fill="var(--red)"/><path d="M10 8v6M10 8a1.5 1.5 0 013 0v4h2" stroke="#fff" stroke-width="1.6" fill="none" stroke-linecap="round"/></svg></div>
  <h3>BE CHOSEN</h3>
  <p>Sed ut perspiciatis unde omnis iste natus error sit voluptatem accusa nt ium doloremque laudant ium, totam rem aperiam, eaque ipsa quae ab illo inventore</p>
</div>
<div class="card" style="left:776px">
  <div class="icon"><svg width="40" height="40" viewBox="0 0 24 24"><circle cx="12" cy="9" r="3.2" fill="var(--red)"/><path d="M6 20c0-4 2.7-6 6-6s6 2 6 6z" fill="var(--red)"/><circle cx="5" cy="6" r="1.6" fill="var(--purple)"/><circle cx="19" cy="6" r="1.6" fill="var(--purple)"/><circle cx="12" cy="2.6" r="1.4" fill="var(--purple)"/></svg></div>
  <h3>SCALE WITH CONFIDENCE</h3>
  <p>Sed ut perspiciatis unde omnis iste natus error sit voluptatem accusa nt ium doloremque laudant ium, totam rem aperiam, eaque ipsa quae ab illo inventore</p>
</div>

<!-- TESTIMONIAL -->
<svg class="testi-bg" viewBox="0 0 1200 800" aria-hidden="true">
  <path d="M60 160Q600 -110 1140 160Q600 -60 60 160Z" fill="var(--purple)"/>
  <path d="M0 250Q600 -30 1200 250V796H0Z" fill="#2f2f31"/>
</svg>
<div class="photo" role="img" aria-label="Business team collaborating around a table, dimmed behind the testimonial" style="left:0;top:2480px;width:1200px;height:676px;background:linear-gradient(90deg,rgba(60,60,62,.3),rgba(90,84,80,.45) 60%,rgba(50,50,52,.3));clip-path:ellipse(120% 100% at 50% 100%)"></div>

<svg class="abs" style="left:162px;top:2636px" width="160" height="138" viewBox="0 0 160 138" aria-hidden="true">
  <path d="M0 138V70Q0 12 62 0V28Q34 36 32 62H66V138Z" fill="#fff"/>
  <path d="M92 138V70Q92 12 154 0V28Q126 36 124 62H158V138Z" fill="#fff"/>
</svg>
<div class="quote-rule"></div>
<p class="testi-text">Sed ut perspiciatis unde omnis iste natus error sit voluptatem accusantium doloremque laudantium, totam rem aperiam, eaque ipsa quae ab illo inventore veritatis et quasi architecto beatae vitae dicta sunt explicabo. Nemo enim ipsam voluptatem quia voluptas sit aspernatur aut odit aut fugit<br><br>Ut enim ad minima veniam, quis nostrum exercitationem ullam corporis</p>
<div class="testi-name">DANIEL HARLOW</div>
<div class="stars">★★★★★</div>

<section class="banner">
  <h2>MARKETING WITHOUT GUESSWORK</h2>
  <p>Too much marketing advice is built on trends, tools, or tactics. Reach Crafters operates differently. We apply academically rigorous frameworks, grounded in real-world execution, to help leaders make better decisions—faster.</p>
  <div class="checks">
    <span><svg width="18" height="18" viewBox="0 0 24 24"><circle cx="12" cy="12" r="11" fill="#fff"/><path d="M7 12.5l3.2 3L17 9" stroke="var(--red)" stroke-width="2.6" fill="none"/></svg>STRATEGY BEFORE TACTICS</span>
    <span><svg width="18" height="18" viewBox="0 0 24 24"><circle cx="12" cy="12" r="11" fill="#fff"/><path d="M7 12.5l3.2 3L17 9" stroke="var(--red)" stroke-width="2.6" fill="none"/></svg>CLARITY OVER COMPLEXITY</span>
  </div>
  <a class="btn btn-purple" style="left:374px;top:306px;width:229px;height:51px">Explore Our Approach</a>
</section>

<!-- HOW WE WORK -->
<h2 class="abs heading" style="left:111px;top:3506px;font-size:46px;line-height:56px">How we work with<br>clients</h2>
<p class="work-text">We help high-ticket service businesses build demand with precision—using rigorous frameworks, market insight, and strategic thinking typically reserved for elite business schools.</p>
<ul class="work-list">
  <li><svg width="16" height="16" viewBox="0 0 24 24"><circle cx="12" cy="12" r="11" fill="var(--ink)"/><path d="M7 12.5l3.2 3L17 9" stroke="#fff" stroke-width="2.6" fill="none"/></svg>Demand Strategy &amp; Positioning</li>
  <li><svg width="16" height="16" viewBox="0 0 24 24"><circle cx="12" cy="12" r="11" fill="var(--ink)"/><path d="M7 12.5l3.2 3L17 9" stroke="#fff" stroke-width="2.6" fill="none"/></svg>Go-to-Market Advisory</li>
  <li><svg width="16" height="16" viewBox="0 0 24 24"><circle cx="12" cy="12" r="11" fill="var(--ink)"/><path d="M7 12.5l3.2 3L17 9" stroke="#fff" stroke-width="2.6" fill="none"/></svg>Executive Marketing Intelligence</li>
  <li><svg width="16" height="16" viewBox="0 0 24 24"><circle cx="12" cy="12" r="11" fill="var(--ink)"/><path d="M7 12.5l3.2 3L17 9" stroke="#fff" stroke-width="2.6" fill="none"/></svg>Fractional / Advisory Support</li>
</ul>
<a class="btn btn-purple" style="left:111px;top:3918px;width:169px;height:43px">View Services</a>

<div class="photo" role="img" aria-label="Consultants reviewing work together at a laptop" style="left:559px;top:3529px;width:252px;height:434px;border-radius:34px;border:3px solid #eee;background:linear-gradient(180deg,#e9ecef 0%,#9aa3ab 45%,#2e3238 100%);box-shadow:0 8px 20px rgba(0,0,0,.15)"></div>
<div class="photo" role="img" aria-label="Hand moving a glowing chess piece amid strategy icons" style="left:837px;top:3458px;width:252px;height:432px;border-radius:34px;border:3px solid #eee;background:radial-gradient(circle at 45% 55%,#e7743a 0%,#3a4a5e 30%,#12202f 70%);box-shadow:0 8px 20px rgba(0,0,0,.15)"></div>

<!-- INSIGHTS -->
<h2 class="abs heading center" style="top:4076px;font-size:46px">Insights for leaders</h2>
<p class="abs center" style="top:4139px;font-size:15.5px;color:var(--grey)">Research-driven perspectives on demand generation, positioning, and growth.</p>

<article class="post" style="left:111px">
  <div class="thumb" role="img" aria-label="Hands reviewing charts on a tablet" style="background:linear-gradient(150deg,#dfe6ee,#7c94b3 50%,#2b3d5a)"></div>
  <p>Ut enim ad minima veniam, quis nostr um exercitationem ullam orpo ris suscipit laboriosam</p>
</article>
<article class="post" style="left:444px">
  <div class="thumb" role="img" aria-label="Team reviewing printed reports at a desk" style="background:linear-gradient(150deg,#cfd1d3,#8c8f93 50%,#3d3f43)"></div>
  <p>Ut enim ad minima veniam, quis nostr um exercitationem ullam orpo ris suscipit laboriosam</p>
</article>
<article class="post" style="left:776px">
  <div class="thumb" role="img" aria-label="Laptop with digital data globe and charts" style="background:linear-gradient(150deg,#c9d6ea,#6f86b4 50%,#1e2c4e)"></div>
  <p>Ut enim ad minima veniam, quis nostr um exercitationem ullam orpo ris suscipit laboriosam</p>
</article>
<a class="btn btn-purple" style="left:529px;top:4656px;width:142px;height:43px">View More</a>

<!-- FOOTER -->
<svg class="foot-bg" viewBox="0 0 1200 432" aria-hidden="true">
  <defs>
    <linearGradient id="footGrad" x1="0" y1="0" x2="0" y2="1">
      <stop offset="0" stop-color="#8f5bf5"/>
      <stop offset="1" stop-color="#7b45ec"/>
    </linearGradient>
  </defs>
  <path d="M60 170Q600 -110 1140 170Q600 -50 60 170Z" fill="var(--red)"/>
  <path d="M0 250Q600 -30 1200 250V432H0Z" fill="url(#footGrad)"/>
</svg>
<div class="abs center foot-logo">REACH CRAFTERS</div>
<nav class="foot-nav">
  <span>HOME</span><span class="sep">|</span>
  <span>ABOUT US</span><span class="sep">|</span>
  <span>SERVICES</span><span class="sep">|</span>
  <span>INSIGHTS</span><span class="sep">|</span>
  <span>CONTACT US</span>
</nav>
<div class="socials" aria-label="Social links"><span></span><span></span><span></span></div>
<p class="abs center copy">(C) Copyright 2026 | All Rights Reserved</p>

</body>
</html>
```